Thornbury Building Company - Card Design

I am looking to use the logo designs that you already did for me to develop a business card. I would like the card to have a black background and be double sided. I want white and green logo and text. I have attached an inspiration photo of a look that I like. I would like to use the Vertical Logo attached to take up the full front side of the card. On the back where I have my name and information, I would like to have the horizontal logo or maybe even just the image of the 'A' and trees without the text. I am open, but I am looking for something clean and simple and I want the green to really pop! Additional files can be found under Design #: 58302946

Target Market(s)

Homeowners

Industry/Entity Type

Construction

Contact Information for Business Card

Name: Marcus Thornbury, Title: Project Manager, Phone: 555.274.8136, Email: thornburybuildingcompany@mailvesta.com, address: 487 Larkspur Ln, Cedarvale, NV 95033, Lic# 2468317

Colors
00AB8E
00BBA5
67D7C9
C6EFE9
E9F9F6

Requirements
Nice to have
• I would like to see the logos that I have already got from ArtLoomHub, though I am open to new ones

```html
<!DOCTYPE html>
<html lang="en">
<head>
<meta charset="utf-8">
<title>Thornbury Building Company – Business Card</title>
<link href="https://fonts.googleapis.com/css2?family=Lato:wght@400;700;900&family=Michroma&display=swap" rel="stylesheet">
<style>
  :root {
    --stage: #d9d9d6;
    --card-black: #231f20;
    --band-white: #ffffff;
    --green: #6ab547;
    --text-white: #ffffff;
    --text-grey: #cfcfcf;
    --text-dark: #231f20;
  }
  * { box-sizing: border-box; margin: 0; padding: 0; }
  html, body {
    width: 1200px; height: 900px; overflow: hidden;
    background: var(--stage);
    font-family: "Lato", sans-serif;
  }
  .stage {
    width: 1200px; height: 900px;
    display: flex; flex-direction: column; align-items: center; justify-content: center;
    gap: 40px;
  }
  .card {
    width: 700px; height: 400px;
    background: var(--card-black);
    border-radius: 22px;
    position: relative;
    overflow: hidden;
  }

  /* Front */
  .front-lockup {
    position: absolute; inset: 0;
    display: flex; align-items: center; justify-content: center; gap: 18px;
  }
  .brand-square {
    width: 46px; height: 46px; background: var(--green); flex: none;
  }
  .brand-name {
    color: var(--text-white);
    font-weight: 900;
    font-size: 38px;
    line-height: 1.1;
    text-transform: uppercase;
    letter-spacing: 1px;
  }
  .est-tag {
    position: absolute;
    font-family: "Michroma", sans-serif;
    color: var(--text-white);
    font-size: 15px;
    letter-spacing: 6px;
    padding: 6px 0;
    border-top: 1.5px solid var(--green);
    border-bottom: 1.5px solid var(--green);
  }
  .est-tag--label { left: 118px; top: 92px; }
  .est-tag--year { right: 118px; bottom: 92px; }

  /* Back */
  .holder {
    position: absolute; left: 48px; top: 42px;
  }
  .holder-name {
    color: var(--green);
    font-weight: 900;
    font-size: 44px;
    letter-spacing: 0.5px;
    text-transform: uppercase;
  }
  .holder-title {
    color: var(--text-grey);
    font-size: 20px;
    margin-top: 2px;
  }
  .info-band {
    position: absolute; left: 0; right: 0; top: 158px; height: 162px;
    background: var(--band-white);
  }
  .contact-list {
    position: absolute; left: 48px; top: 22px;
    list-style: none;
    color: var(--text-dark);
    font-size: 17px;
    line-height: 1.3;
  }
  .contact-item { display: flex; align-items: flex-start; gap: 12px; margin-bottom: 8px; }
  .contact-icon { width: 18px; height: 18px; flex: none; margin-top: 2px; }
  .band-brand {
    position: absolute; right: 40px; top: 44px;
    display: flex; align-items: center; gap: 12px;
  }
  .band-brand .brand-square { width: 30px; height: 30px; }
  .band-brand .brand-name { color: var(--green); font-size: 20px; line-height: 1.15; }
  .licence {
    position: absolute; left: 48px; bottom: 30px;
    color: var(--text-grey);
    font-size: 18px;
  }
</style>
</head>
<body>
<main class="stage">

  <section class="card card--front" aria-label="Card front">
    <span class="est-tag est-tag--label">ESTD</span>
    <div class="front-lockup">
      <span class="brand-square" aria-hidden="true"></span>
      <p class="brand-name">Thornbury<br>Building Company</p>
    </div>
    <span class="est-tag est-tag--year">2020</span>
  </section>

  <section class="card card--back" aria-label="Card back">
    <div class="holder">
      <h1 class="holder-name">Marcus Thornbury</h1>
      <p class="holder-title">Project Manager</p>
    </div>

    <div class="info-band">
      <ul class="contact-list">
        <li class="contact-item">
          <svg class="contact-icon" viewBox="0 0 24 24" aria-hidden="true"><path fill="#6ab547" d="M12 1a8 8 0 0 0-8 8c0 6 8 14 8 14s8-8 8-14a8 8 0 0 0-8-8zm0 11a3 3 0 1 1 0-6 3 3 0 0 1 0 6z"/></svg>
          <span>487 Larkspur Ln<br>Cedarvale, NV 95033</span>
        </li>
        <li class="contact-item">
          <svg class="contact-icon" viewBox="0 0 24 24" aria-hidden="true"><path fill="#6ab547" d="M6.6 10.8a15 15 0 0 0 6.6 6.6l2.2-2.2a1 1 0 0 1 1-.25 11.4 11.4 0 0 0 3.6.57 1 1 0 0 1 1 1V20a1 1 0 0 1-1 1A17 17 0 0 1 3 4a1 1 0 0 1 1-1h3.5a1 1 0 0 1 1 1c0 1.25.2 2.45.57 3.6a1 1 0 0 1-.25 1z"/></svg>
          <span>555.274.8136</span>
        </li>
        <li class="contact-item">
          <svg class="contact-icon" viewBox="0 0 24 24" aria-hidden="true"><path fill="#6ab547" d="M2 5h20v14H2z"/><path fill="none" stroke="#fff" stroke-width="1.6" d="M2 5l10 8 10-8"/></svg>
          <span>thornburybuildingcompany@mailvesta.com</span>
        </li>
      </ul>
      <div class="band-brand">
        <span class="brand-square" aria-hidden="true"></span>
        <p class="brand-name">Thornbury<br>Building Co.</p>
      </div>
    </div>

    <p class="licence">Lic# 2468317</p>
  </section>

</main>
</body>
</html>
```